Weightloss company needs Business Card

We want a business card that is clean and professional, yet portrays that we are a friendly, innovative, and versatile program designed to fit the needs of our clients.
I would like there to be 2 sides, one side having an appointment card, and the other side containing the logo and business information. There can be decorations on both sides. The logo is attached.

Target Market(s)

Men and women 40-60

Industry/Entity Type

Business

Contact Information for Business Card

Font styles to use
Sans Serif

Requirements
Must have
• The logo, space for business information
Nice to have
• The colors in the logo
Should not have
• No pictures of people or food

```html
<!DOCTYPE html>
<html lang="en">
<head>
<meta charset="utf-8">
<title>Riseturn Wellness – Business Card</title>
<link rel="stylesheet" href="https://fonts.googleapis.com/css2?family=Questrial&display=swap">
<style>
  :root{
    --bg:#2b2b2d;
    --card:#ffffff;
    --red:#e8213a;
    --blue:#4fc6ee;
    --ink:#1d1d1f;
    --white:#ffffff;
  }
  *{margin:0;padding:0;box-sizing:border-box}
  html,body{width:1200px;height:900px;overflow:hidden;background:var(--bg)}
  body{position:relative;font-family:"Questrial",Arial,sans-serif}

  .card{
    position:absolute;width:620px;height:355px;
    background:var(--card);border-radius:22px;overflow:hidden;
    box-shadow:0 10px 30px rgba(0,0,0,.45);
  }
  .card--appointment{left:80px;top:50px}
  .card--contact{left:500px;top:480px}

  .brand{
    position:absolute;right:38px;top:42px;
    display:flex;align-items:center;gap:10px;
    color:var(--red);font-size:30px;letter-spacing:.5px;
  }
  .brand__dot{width:18px;height:18px;border-radius:50%;background:var(--red)}

  .appointment{position:absolute;left:48px;top:178px;width:520px}
  .appointment__title{color:var(--red);font-size:15px;letter-spacing:.5px;margin-bottom:14px}
  .field{display:flex;align-items:flex-end;gap:10px;height:40px;font-size:16px;color:var(--ink)}
  .field__line{flex:1;border-bottom:1.5px solid var(--ink);height:1px;margin-bottom:5px}

  .contact__shape{position:absolute;left:0;top:0}
  .contact__info{position:absolute;left:170px;top:192px;color:var(--white);font-size:15px;line-height:1.3}
  .contact__name{color:var(--red);font-size:26px;letter-spacing:.5px;line-height:1.1}
  .contact__role{font-size:15px;margin-bottom:10px}
  .contact__address{margin-bottom:8px}
  .contact__row{display:flex;align-items:center;gap:10px}
  .contact__row svg{width:14px;height:14px;flex:none}
</style>
</head>
<body>

<section class="card card--appointment">
  <div class="brand"><span class="brand__dot"></span>Riseturn Wellness</div>
  <div class="appointment">
    <p class="appointment__title">APPOINTMENT</p>
    <div class="field"><span>Name:</span><span class="field__line"></span></div>
    <div class="field"><span>Date:</span><span class="field__line"></span></div>
    <div class="field"><span>Time:</span><span class="field__line"></span></div>
  </div>
</section>

<section class="card card--contact">
  <svg class="contact__shape" width="620" height="355" viewBox="0 0 620 355">
    <path d="M20 355 A260 260 0 0 1 540 355 Z" fill="var(--red)" stroke="var(--ink)" stroke-width="2"/>
    <path d="M48 355 A232 232 0 0 1 512 355 Z" fill="var(--blue)" stroke="var(--ink)" stroke-width="1.5"/>
  </svg>
  <div class="brand"><span class="brand__dot"></span>Riseturn Wellness</div>
  <div class="contact__info">
    <p class="contact__name">MARLO BENNETT</p>
    <p class="contact__role">DIRECTOR</p>
    <p class="contact__address">Harbor Lane, 40218<br>Coastview, Nordland</p>
    <p class="contact__row">
      <svg viewBox="0 0 24 24"><path fill="var(--red)" d="M6.6 10.8a15 15 0 0 0 6.6 6.6l2.2-2.2c.3-.3.7-.4 1-.2 1.1.4 2.3.6 3.6.6.6 0 1 .4 1 1V20c0 .6-.4 1-1 1A17 17 0 0 1 3 4c0-.6.4-1 1-1h3.5c.6 0 1 .4 1 1 0 1.3.2 2.5.6 3.6.1.3 0 .7-.2 1z"/></svg>
      +330 5817-2043</p>
    <p class="contact__row">
      <svg viewBox="0 0 24 24"><rect x="3" y="5" width="18" height="14" rx="1.5" fill="none" stroke="var(--red)" stroke-width="2"/><path d="M3 6l9 7 9-7" fill="none" stroke="var(--red)" stroke-width="2"/></svg>
      info@riseturnwellness.com</p>
    <p class="contact__row">
      <svg viewBox="0 0 24 24"><circle cx="12" cy="12" r="9" fill="none" stroke="var(--red)" stroke-width="2"/><path d="M3 12h18M12 3c3 3 3 15 0 18M12 3c-3 3-3 15 0 18" fill="none" stroke="var(--red)" stroke-width="1.6"/></svg>
      www.riseturnwellness.com</p>
  </div>
</section>

</body>
</html>
```